Business Card Design for Software Development Company

I am looking for a business card design the incorporates my new logo (attached below).

Key information to include:
Name: Martin Quelbrook
Title: CEO
Email: martin@brightwellcivic.example
Phone: 555-218-9403
Website: www.brightwellcivic.example

NOTE: This design should be easy to edit so that we can order cards for different members of our team.

```html
<!DOCTYPE html>
<html lang="en">
<head>
<meta charset="utf-8">
<title>BrightwellLabs — Business Card</title>
<link href="https://fonts.googleapis.com/css2?family=Montserrat:wght@400;600;700&family=Open+Sans:wght@400&display=swap" rel="stylesheet">
<style>
  :root {
    --backdrop: #26282b;
    --card: #ffffff;
    --ink: #1d1d1f;
    --muted: #555a60;
    --teal: #14bfa9;
    --teal-deep: #16968a;
    --orange: #ee8427;
    --peach: #f7c08c;
    --red: #b3242c;
  }
  html, body {
    margin: 0;
    width: 1200px;
    height: 900px;
    overflow: hidden;
    background: var(--backdrop);
  }
  .canvas {
    width: 1200px;
    height: 900px;
    display: flex;
    align-items: center;
    justify-content: center;
    gap: 60px;
  }
  .card {
    position: relative;
    width: 520px;
    height: 298px;
    background: var(--card);
    border-radius: 22px;
    overflow: hidden;
    box-shadow: 0 10px 30px rgba(0,0,0,.45);
    font-family: "Open Sans", Arial, sans-serif;
  }
  /* Front: contact side */
  .wordmark {
    font-family: "Montserrat", Arial, sans-serif;
    font-weight: 600;
    color: var(--ink);
    letter-spacing: -0.5px;
    line-height: 1;
  }
  .front .brand { position: absolute; left: 40px; top: 34px; }
  .front .wordmark { font-size: 38px; }
  .tagline {
    font-family: "Montserrat", Arial, sans-serif;
    font-weight: 600;
    font-size: 6px;
    letter-spacing: 0.4px;
    text-transform: uppercase;
    color: var(--ink);
    text-align: right;
    margin-top: 3px;
  }
  .person { position: absolute; left: 40px; top: 112px; }
  .person-name {
    font-family: "Montserrat", Arial, sans-serif;
    font-weight: 600;
    font-size: 17px;
    letter-spacing: 0.5px;
    text-transform: uppercase;
    margin: 0;
  }
  .person-name .first { color: var(--teal); }
  .person-name .last { color: var(--orange); }
  .person-title { font-size: 13px; color: var(--muted); margin: 4px 0 8px; }
  .social { display: flex; gap: 6px; margin-bottom: 10px; }
  .social span { width: 12px; height: 12px; border-radius: 50%; }
  .social .s1 { background: #e8594f; }
  .social .s2 { background: var(--teal); }
  .social .s3 { background: var(--orange); }
  .contact { margin: 0; padding: 0; list-style: none; font-size: 13px; color: var(--muted); line-height: 1.55; }
  .symbol-area {
    position: absolute;
    right: 30px;
    top: 80px;
    width: 160px;
    height: 190px;
    border-radius: 8px;
    background: linear-gradient(160deg, var(--teal) 0%, var(--red) 50%, var(--orange) 100%);
    opacity: .9;
  }
  /* Back: logo side */
  .back .wash {
    position: absolute;
    inset: 0;
    background: linear-gradient(135deg, rgba(20,191,169,.12) 0%, rgba(247,192,140,.14) 50%, rgba(255,255,255,0) 80%);
  }
  .back .brand {
    position: absolute;
    left: 50%;
    top: 50%;
    transform: translate(-50%, -50%);
  }
  .back .lockup { display: flex; align-items: center; gap: 12px; }
  .back .mark-square { width: 26px; height: 26px; background: var(--teal); }
  .back .wordmark { font-size: 54px; }
  .back .tagline { font-size: 7px; }
</style>
</head>
<body>
<main class="canvas">
  <section class="card front">
    <div class="brand">
      <div class="wordmark">BrightwellLabs</div>
      <div class="tagline">A division of Brightwell Civic</div>
    </div>
    <div class="person">
      <h1 class="person-name"><span class="first">Martin</span> <span class="last">Quelbrook</span></h1>
      <p class="person-title">CEO</p>
      <div class="social" aria-label="Social links">
        <span class="s1"></span><span class="s2"></span><span class="s3"></span>
      </div>
      <ul class="contact">
        <li>555-218-9403</li>
        <li>martin@brightwellcivic.example</li>
        <li>www.brightwellcivic.example</li>
      </ul>
    </div>
    <div class="symbol-area" role="img" aria-label="Company logo symbol in teal, red and orange"></div>
  </section>

  <section class="card back">
    <div class="wash"></div>
    <div class="brand">
      <div class="lockup">
        <span class="mark-square"></span>
        <div class="wordmark">BrightwellLabs</div>
      </div>
      <div class="tagline">A division of Brightwell Civic</div>
    </div>
  </section>
</main>
</body>
</html>
```